Web Developer Needs a Business Card Design

I need a personal business card design that represents me as a web developer for potential employers. I would like the background to be a dark color on the front for contrast with my logo and name. The back will have all my information along with a smaller version of the logo. I want something with a modern look and feel, not too conservative. This will be used for potential employers and freelance work.

Industry/Entity Type

Business

Contact Information for Business Card

Front should have my logo and name. The back should have all my personal information which would include: name: Tom Varulek, phone: 570-614-3098, email: tomvarulek@quillbox.net, website url: www.tomvarulek.net, logo, web developer.

Font styles to use
Sans Serif

Requirements
Must have
• Must include my logo. The color palette base color will be the logo color.

```html
<!DOCTYPE html>
<html lang="en">
<head>
<meta charset="utf-8">
<title>Tom Varulek — Business Card</title>
<link rel="stylesheet" href="https://fonts.googleapis.com/css2?family=Source+Sans+3:wght@400;600;700&display=swap">
<style>
  :root {
    --teal: #7fd0c0;
    --teal-soft: #a6ddd2;
    --card-light: #f4f5f4;
    --card-dark: #232323;
    --backdrop: #d9d6d0;
    --ring-faint: rgba(127, 208, 192, 0.10);
  }
  * { margin: 0; padding: 0; box-sizing: border-box; }
  html, body {
    width: 1200px; height: 780px; overflow: hidden;
    background: var(--backdrop);
    font-family: "Source Sans 3", sans-serif;
  }
  .stage {
    width: 1200px; height: 780px;
    display: flex; align-items: center; justify-content: center; gap: 50px;
  }
  .card {
    position: relative;
    width: 525px; height: 300px;
    border-radius: 3px;
    overflow: hidden;
    box-shadow: 0 10px 26px rgba(0,0,0,0.22);
  }
  /* Back side: contact details */
  .card--back {
    background: radial-gradient(circle at 50% 55%, #ffffff 0%, var(--card-light) 70%);
    display: flex; align-items: center;
    padding: 0 44px;
    gap: 26px;
  }
  .card--back .faint-ring {
    position: absolute; left: 50%; top: 50%;
    width: 360px; height: 360px;
    transform: translate(-50%, -50%);
    border-radius: 50%;
    border: 34px solid var(--ring-faint);
  }
  .brand {
    position: relative;
    display: flex; flex-direction: column; align-items: center; gap: 8px;
    color: var(--teal);
    font-weight: 700;
  }
  .brand__circle {
    width: 96px; height: 96px; border-radius: 50%;
    border: 7px solid var(--teal);
  }
  .brand__name { font-size: 17px; letter-spacing: 0.04em; }
  .identity { position: relative; color: var(--teal); }
  .identity__name { font-size: 30px; font-weight: 700; line-height: 1; }
  .identity__role { font-size: 17px; font-weight: 400; margin-top: 4px; }
  .contact {
    list-style: none; margin-top: 22px;
    font-size: 16px; line-height: 1.3; color: var(--teal);
  }
  /* Front side: name and brand */
  .card--front {
    background: radial-gradient(circle at 65% 45%, #2e2e2e 0%, var(--card-dark) 75%);
    display: flex; align-items: center; justify-content: space-between;
    padding: 0 56px;
  }
  .card--front .identity__name { font-size: 30px; color: var(--teal); }
  .card--front .brand__circle { width: 170px; height: 170px; border-width: 11px; }
  .card--front .brand__name { font-size: 22px; }
</style>
</head>
<body>
  <main class="stage">
    <section class="card card--back" aria-label="Card back">
      <div class="faint-ring"></div>
      <div class="brand">
        <div class="brand__circle"></div>
        <span class="brand__name">Varulek</span>
      </div>
      <div class="identity">
        <h1 class="identity__name">Tom Varulek</h1>
        <p class="identity__role">Managing Director</p>
        <ul class="contact">
          <li>570-614-3098</li>
          <li>tomvarulek@quillbox.net</li>
          <li>www.tomvarulek.net</li>
        </ul>
      </div>
    </section>

    <section class="card card--front" aria-label="Card front">
      <div class="identity">
        <h2 class="identity__name">Tom Varulek</h2>
      </div>
      <div class="brand">
        <div class="brand__circle"></div>
        <span class="brand__name">Varulek</span>
      </div>
    </section>
  </main>
</body>
</html>
```